Automotive Accessories Business Card

Design a business template that match our new logo design and our industry.

https://www.qelmotorgear.com/

Target Market(s)

Aftermarket auto parts and accessories

Industry/Entity Type

automotive

Contact Information for Business Card

company logo

Font styles to use
Serif
Sans Serif

Colors
EB3D1F
EC4F4E
F09395
F8D3D4
FCEDEE

```html
<!DOCTYPE html>
<html lang="en">
<head>
<meta charset="utf-8">
<title>Qel Motorgear – Business Card</title>
<link rel="stylesheet" href="https://fonts.googleapis.com/css2?family=Poppins:wght@400;500;700&display=swap">
<style>
  :root {
    --stage: #2b2b2d;
    --card-white: #ffffff;
    --card-black: #151516;
    --pattern-dark: #232325;
    --pattern-light: #3a3a3d;
    --brand-red: #e0202a;
    --ink: #1b1b1b;
    --ink-grey: #4a4a4c;
    --rule: #9a9a9a;
  }
  * { box-sizing: border-box; margin: 0; padding: 0; }
  html, body { width: 1200px; height: 1108px; overflow: hidden; }
  body {
    background: var(--stage);
    font-family: "Poppins", Arial, sans-serif;
    position: relative;
  }
  .card {
    position: absolute;
    top: 234px;
    width: 400px;
    height: 640px;
    border-radius: 26px;
    overflow: hidden;
  }
  .card--front {
    left: 150px;
    background: var(--card-white);
    color: var(--ink);
    text-align: center;
  }
  .card--back {
    left: 650px;
    background: var(--card-black);
  }
  .brand {
    position: absolute;
    top: 120px;
    left: 0; right: 0;
    display: flex;
    align-items: center;
    justify-content: center;
    gap: 12px;
  }
  .brand__mark {
    width: 22px; height: 22px;
    background: var(--brand-red);
  }
  .brand__name {
    font-weight: 700;
    font-size: 34px;
    letter-spacing: 1px;
    color: var(--ink-grey);
    text-transform: uppercase;
    line-height: 1.1;
  }
  .brand__sub {
    position: absolute;
    top: 170px; left: 0; right: 0;
    font-size: 14px;
    font-weight: 500;
    letter-spacing: 3px;
    color: var(--ink-grey);
    text-transform: uppercase;
  }
  .person {
    position: absolute;
    top: 330px; left: 0; right: 0;
  }
  .person__name {
    font-weight: 700;
    font-size: 30px;
    color: var(--brand-red);
    text-transform: uppercase;
    letter-spacing: 0.5px;
    line-height: 1.1;
  }
  .person__role {
    font-size: 18px;
    color: var(--ink);
    margin-top: 2px;
  }
  .icon-row {
    position: absolute;
    top: 420px; left: 40px; right: 40px;
    display: flex;
    align-items: center;
    gap: 10px;
  }
  .icon-row__rule { flex: 1; height: 1px; background: var(--rule); }
  .icon {
    width: 30px; height: 30px;
    border-radius: 5px;
    background: var(--brand-red);
    display: flex; align-items: center; justify-content: center;
  }
  .contact {
    position: absolute;
    top: 466px; left: 0; right: 0;
    font-size: 18px;
    line-height: 1.45;
  }
  .contact__accent { color: var(--brand-red); }
  .divider {
    position: absolute;
    top: 570px; left: 40px; right: 40px;
    height: 1px; background: var(--rule);
  }
  .address {
    position: absolute;
    top: 584px; left: 0; right: 0;
    font-size: 16px;
    line-height: 1.35;
  }
  .back__texture {
    position: absolute; inset: 0;
    background: linear-gradient(135deg, var(--pattern-dark) 0%, var(--pattern-light) 55%, var(--pattern-dark) 100%);
  }
  .back__brand {
    position: absolute;
    top: 400px; left: 0; right: 0;
    display: flex; align-items: center; justify-content: center; gap: 10px;
  }
  .back__mark { width: 16px; height: 16px; background: var(--brand-red); }
  .back__name {
    font-weight: 700;
    font-size: 30px;
    color: var(--card-white);
    letter-spacing: 1px;
  }
</style>
</head>
<body>
  <section class="card card--front">
    <div class="brand">
      <span class="brand__mark"></span>
      <span class="brand__name">Qel Motorgear</span>
    </div>
    <div class="brand__sub">Qel Motorgear Inc</div>

    <div class="person">
      <div class="person__name">Daniel Reyes</div>
      <div class="person__role">Managing Director</div>
    </div>

    <div class="icon-row">
      <span class="icon-row__rule"></span>
      <span class="icon" aria-label="Phone">
        <svg width="18" height="18" viewBox="0 0 24 24"><path fill="#fff" d="M6.6 10.8a15 15 0 0 0 6.6 6.6l2.2-2.2c.3-.3.7-.4 1-.2 1.1.4 2.3.6 3.6.6.6 0 1 .4 1 1V20c0 .6-.4 1-1 1A17 17 0 0 1 3 4c0-.6.4-1 1-1h3.5c.6 0 1 .4 1 1 0 1.3.2 2.5.6 3.6.1.3 0 .7-.2 1z"/></svg>
      </span>
      <span class="icon" aria-label="Email">
        <svg width="18" height="18" viewBox="0 0 24 24"><rect x="3" y="5" width="18" height="14" rx="1.5" fill="none" stroke="#fff" stroke-width="2"/><path d="M3 6l9 7 9-7" fill="none" stroke="#fff" stroke-width="2"/></svg>
      </span>
      <span class="icon" aria-label="Website">
        <svg width="18" height="18" viewBox="0 0 24 24"><circle cx="12" cy="12" r="9" fill="none" stroke="#fff" stroke-width="2"/><path d="M3 12h18M12 3c3 3 3 15 0 18M12 3c-3 3-3 15 0 18" fill="none" stroke="#fff" stroke-width="1.5"/></svg>
      </span>
      <span class="icon-row__rule"></span>
    </div>

    <div class="contact">
      <div>055-287 314 602</div>
      <div>info@qelmotorgear.com</div>
      <div>www.<span class="contact__accent">qelmotorgear</span>.com</div>
    </div>

    <div class="divider"></div>

    <div class="address">
      <div>318, Westmere Garage Row</div>
      <div>60218, Northvale Bay</div>
    </div>
  </section>

  <section class="card card--back">
    <div class="back__texture" role="img" aria-label="Repeating embossed brand-name pattern in dark greys"></div>
    <div class="back__brand">
      <span class="back__mark"></span>
      <span class="back__name">QEL</span>
    </div>
  </section>
</body>
</html>
```